Create a memorable Stationary for Security Software Company

Velbrantix is the worldwide leader in securing the Internet. Making Internet communications and critical data secure, reliable and available everywhere has been and continues to be our ongoing vision. We are committed to staying focused on real customer needs and to developing new and innovative security solutions that redefine the security landscape.

Industry/Entity Type

Internet

Font styles to use
Serif
Sans Serif
Script

Colors
0792cd
33a6d7
85cae6

```html
<!DOCTYPE html>
<html lang="en">
<head>
<meta charset="utf-8">
<title>Velbrantix Business Card</title>
<link href="https://fonts.googleapis.com/css2?family=Open+Sans:wght@400;600;700&display=swap" rel="stylesheet">
<style>
  :root {
    --blue-deep: #0792cd;
    --blue-mid: #33a6d7;
    --blue-soft: #85cae6;
    --blue-pale: #dcedf6;
    --ink: #000000;
    --text-dark: #2a2a2a;
    --paper: #ffffff;
    --backdrop: #e9ecef;
  }
  * { margin: 0; padding: 0; box-sizing: border-box; }
  html, body { width: 1200px; height: 1120px; overflow: hidden; }
  body {
    background: var(--backdrop);
    font-family: "Open Sans", sans-serif;
    position: relative;
  }
  .card {
    position: absolute;
    left: 250px;
    width: 700px;
    height: 400px;
    overflow: hidden;
    box-shadow: 0 8px 24px rgba(0,0,0,0.18);
  }
  /* Front card */
  .card-front { top: 90px; background: var(--paper); }
  .front-pattern {
    position: absolute; inset: 0;
    background: linear-gradient(135deg, var(--blue-pale) 0%, #f2f8fc 50%, var(--blue-pale) 100%);
    opacity: 0.75;
  }
  .front-brand {
    position: absolute; left: 0; right: 0; top: 130px;
    display: flex; align-items: center; justify-content: center; gap: 16px;
  }
  .brand-dot {
    width: 46px; height: 46px; border-radius: 50%;
    background: var(--blue-mid);
  }
  .brand-name {
    font-weight: 700;
    font-size: 48px;
    color: var(--blue-mid);
    line-height: 1;
  }
  .front-web {
    position: absolute; left: 0; right: 0; top: 305px;
    text-align: center;
    font-size: 22px;
    letter-spacing: 4px;
    color: var(--text-dark);
  }
  /* Back card */
  .card-back { top: 600px; background: var(--ink); color: var(--paper); }
  .back-waves { position: absolute; inset: 0; }
  .holder {
    position: absolute; right: 40px; top: 26px; text-align: right;
  }
  .holder-name { font-weight: 700; font-size: 20px; line-height: 1.2; }
  .holder-title { font-size: 17px; color: var(--blue-mid); line-height: 1.2; }
  .back-brand {
    position: absolute; left: 60px; top: 130px;
    display: flex; align-items: center; gap: 14px;
  }
  .back-brand .brand-name { font-size: 40px; }
  .back-brand .brand-dot { width: 38px; height: 38px; }
  .address {
    position: absolute; left: 130px; top: 240px;
    font-size: 17px; line-height: 1.35;
  }
  .contact {
    position: absolute; right: 32px; top: 228px;
    list-style: none; text-align: right;
    font-size: 16px; line-height: 1.7;
  }
  .contact li { display: flex; align-items: center; justify-content: flex-end; gap: 8px; }
  .contact svg { width: 14px; height: 14px; fill: var(--paper); }
</style>
</head>
<body>
  <section class="card card-front">
    <div class="front-pattern" role="img" aria-label="Faint repeating brand pattern across the card face"></div>
    <div class="front-brand">
      <span class="brand-dot"></span>
      <span class="brand-name">Velbrantix</span>
    </div>
    <p class="front-web">www.velbrantix.com</p>
  </section>

  <section class="card card-back">
    <svg class="back-waves" viewBox="0 0 700 400" preserveAspectRatio="none">
      <path class="wave-fill" d="M0 400 L0 372 C180 350 380 345 500 280 C580 238 640 192 700 170 L700 400 Z" fill="var(--blue-deep)"/>
      <path class="wave-band" d="M0 340 C240 330 430 325 545 250 C610 206 660 172 700 158 L700 168 C662 182 615 214 552 258 C435 338 240 345 0 354 Z" fill="var(--blue-mid)"/>
      <path class="wave-line" d="M90 318 C300 316 440 305 540 245 C605 205 655 172 700 160" fill="none" stroke="var(--blue-mid)" stroke-width="3"/>
    </svg>
    <div class="holder">
      <p class="holder-name">Your Name</p>
      <p class="holder-title">Title</p>
    </div>
    <div class="back-brand">
      <span class="brand-dot"></span>
      <span class="brand-name">Velbrantix</span>
    </div>
    <p class="address">Street Name, City Name<br>Zipcode-012345</p>
    <ul class="contact">
      <li><svg viewBox="0 0 16 16"><path d="M3 1h3l1 4-2 1.5a9 9 0 0 0 4.5 4.5L11 9l4 1v3a2 2 0 0 1-2 2A12 12 0 0 1 1 3a2 2 0 0 1 2-2z"/></svg>012-345-6789</li>
      <li><svg viewBox="0 0 16 16"><path d="M4 0h8a1 1 0 0 1 1 1v14a1 1 0 0 1-1 1H4a1 1 0 0 1-1-1V1a1 1 0 0 1 1-1zm1 2v10h6V2zm3 11a1 1 0 1 0 0 2 1 1 0 0 0 0-2z"/></svg>012-345-6789</li>
      <li><svg viewBox="0 0 16 16"><path d="M1 3h14v10H1zm1 1 6 5 6-5z"/></svg>info@velbrantix.com</li>
      <li><svg viewBox="0 0 16 16"><path d="M8 0a8 8 0 1 0 0 16A8 8 0 0 0 8 0zm0 1.5c1 1 1.7 3 1.9 5.5H6.1C6.3 4.5 7 2.5 8 1.5zM1.6 7a6.5 6.5 0 0 1 3.5-5C4.6 3.3 4.2 5 4.1 7zm0 2h2.5c.1 2 .5 3.7 1 5a6.5 6.5 0 0 1-3.5-5zM8 14.5c-1-1-1.7-3-1.9-5.5h3.8c-.2 2.5-.9 4.5-1.9 5.5zm2.9-.5c.5-1.3.9-3 1-5h2.5a6.5 6.5 0 0 1-3.5 5zm1-7c-.1-2-.5-3.7-1-5a6.5 6.5 0 0 1 3.5 5z"/></svg>www.velbrantix.com</li>
    </ul>
  </section>
</body>
</html>
```